Roofing Contractor business card redesign

I want to redesign my business card with a fresh, eye catching concept

Target Market(s)

Residential Roofing Clients, potential employees, and subcontractors.

Industry/Entity Type

Business

Colors

Designer to choose colors to be used in the design.

Requirements
Nice to have
• I just want something that's more pleasing to the eye. You can use a combination of either / or of my logos.

```html
<!DOCTYPE html>
<html lang="en">
<head>
<meta charset="utf-8">
<title>Fairway Builders – Business Card</title>
<link href="https://fonts.googleapis.com/css2?family=Roboto:wght@400;500;700;900&family=Roboto+Condensed:wght@700&display=swap" rel="stylesheet">
<style>
  :root {
    --bg: #e9e6e1;
    --card-white: #ffffff;
    --card-black: #1d1f20;
    --maroon: #5a1d16;
    --orange: #e8741e;
    --ink: #3a3a3a;
    --rule: #8a8a8a;
    --muted: #cfcfcf;
  }
  * { margin: 0; padding: 0; box-sizing: border-box; }
  html, body { width: 1200px; height: 911px; overflow: hidden; }
  body {
    background: var(--bg);
    font-family: "Roboto", Arial, sans-serif;
    position: relative;
  }
  .card {
    position: absolute;
    width: 525px;
    height: 300px;
    border-radius: 18px;
    box-shadow: 0 10px 28px rgba(0,0,0,.22);
    overflow: hidden;
  }
  /* Front */
  .card-front { left: 50px; top: 305px; background: var(--card-white); }
  .brand {
    position: absolute; right: 34px; top: 34px;
    text-align: left;
  }
  .brand-row { display: flex; align-items: center; gap: 10px; }
  .brand-name {
    font-family: "Roboto Condensed", Arial, sans-serif;
    font-weight: 700; font-size: 34px; color: var(--maroon);
    letter-spacing: -0.5px; line-height: 1;
  }
  .brand-dot {
    width: 30px; height: 30px; border-radius: 50%;
    background: var(--maroon);
  }
  .brand-sub {
    font-family: "Roboto Condensed", Arial, sans-serif;
    font-weight: 700; font-size: 17px; color: var(--maroon);
    margin-top: 4px; text-align: right;
  }
  .details {
    position: absolute; left: 30px; bottom: 26px;
    display: flex; gap: 16px;
  }
  .icon-col {
    display: flex; flex-direction: column; justify-content: space-between;
    align-items: center; padding: 4px 0; width: 18px;
  }
  .icon-col svg { width: 14px; height: 14px; fill: var(--maroon); }
  .icon-row { display: flex; flex-direction: column; gap: 4px; align-items: center; }
  .info {
    border-left: 1px solid var(--rule);
    padding-left: 14px;
    font-size: 12.5px; color: var(--ink); line-height: 1.35;
  }
  .person { font-weight: 700; font-size: 15px; color: var(--ink); letter-spacing: .2px; }
  .role { color: var(--orange); font-size: 14px; line-height: 1.3; }
  .group { margin-top: 10px; }
  /* Back */
  .card-back { left: 625px; top: 305px; background: var(--card-black); }
  .back-url {
    position: absolute; left: 38px; top: 50%;
    transform: translate(-50%, -50%) rotate(90deg);
    transform-origin: center;
    color: var(--muted); font-size: 12px; letter-spacing: 5px;
    white-space: nowrap; margin-left: 10px;
  }
  .back-emblem {
    position: absolute; left: 50%; top: 50%;
    width: 150px; height: 150px; transform: translate(-50%, -50%);
    border-radius: 50%;
    border: 3px solid #f3ece4;
    background: radial-gradient(circle at 55% 45%, #f0a640 0%, #d9661c 45%, #4a1a14 80%);
  }
</style>
</head>
<body>

<section class="card card-front" aria-label="Business card front">
  <div class="brand">
    <div class="brand-row">
      <span class="brand-name">Fairway Builders</span>
      <span class="brand-dot"></span>
    </div>
    <div class="brand-sub">General Contractors, Inc.</div>
  </div>

  <div class="details">
    <div class="icon-col">
      <svg viewBox="0 0 16 16" aria-hidden="true"><circle cx="8" cy="5" r="3.5"/><path d="M1.5 16c0-4 3-6 6.5-6s6.5 2 6.5 6z"/></svg>
      <svg viewBox="0 0 16 16" aria-hidden="true"><path d="M8 0a5.5 5.5 0 0 0-5.5 5.5C2.5 10 8 16 8 16s5.5-6 5.5-10.5A5.5 5.5 0 0 0 8 0zm0 8a2.5 2.5 0 1 1 0-5 2.5 2.5 0 0 1 0 5z"/></svg>
      <div class="icon-row">
        <svg viewBox="0 0 16 16" aria-hidden="true"><path d="M3.6 1l2.4 3-1.5 1.8a9 9 0 0 0 5.7 5.7l1.8-1.5 3 2.4-1.6 2.6C7.6 15 1 8.4 1 2.6z"/></svg>
        <svg viewBox="0 0 16 16" aria-hidden="true"><path d="M1 3h14v10H1zm1.5 1.5v7h11v-7z"/></svg>
        <svg viewBox="0 0 16 16" aria-hidden="true"><path d="M1 3h14v10H1zm1 1l6 5 6-5z"/></svg>
        <svg viewBox="0 0 16 16" aria-hidden="true"><circle cx="8" cy="8" r="7"/></svg>
      </div>
    </div>
    <div class="info">
      <div class="person">SAM HARLOW</div>
      <div class="role">Keller Certified Roof Inspector</div>
      <div class="role">Licensed Property Adjuster</div>
      <div class="group">4410 Meadow Lane Suite 120<br>Plano, TX 75093</div>
      <div class="group">(555) 210-4800<br>(555) 318-2290<br>sam@fairwaytx.com<br>www.fairwaytx.com</div>
    </div>
  </div>
</section>

<section class="card card-back" aria-label="Business card back">
  <div class="back-url">www.fairwaytx.com</div>
  <div class="back-emblem" role="img" aria-label="Circular illustration of three roofing workers with tools"></div>
</section>

</body>
</html>
```